Make a high end Clubcard for personal training studio. Not a business card but a clubcard

Important! Not a business card buT a clubcard

I need club cards for my clients to check in. My personal training studio is a high end studio with high prices so it needs to look classy and expensive.

You can use the attachment that you like.

the website url needs to be on the card www.Vorniqfit.nl

The card needs to have 2 way design.

I will choose the best Design and have more projects for the winner

Place the following text on the one side of the card:

Personal Training Studio Marwijk

personal training and fitness

Fitness

53,9 x 85,7mm

• Classy and expensive
• Classy and expensive

```html
<!DOCTYPE html>
<html lang="en">
<head>
<meta charset="utf-8">
<title>Vorniq fit — Club card, front and back</title>
<link rel="stylesheet" href="https://fonts.googleapis.com/css2?family=Alfa+Slab+One&family=Roboto+Slab:wght@700;800;900&family=Cinzel:wght@500&family=Tinos:wght@400;700&display=swap">
<style>
  :root {
    --stage: #2b2b2d;
    --card-light: #e4e3e5;
    --card-light-tone: #cdbfb8;
    --card-dark: #120c0b;
    --swirl-red: #6e1e10;
    --swirl-deep: #3a100a;
    --brand-red: #d1232a;
    --ink: #111111;
    --ink-soft: #3a3a3c;
    --silver: #d3d3d5;
    --silver-soft: #b9b6b6;
  }
  * { margin: 0; padding: 0; box-sizing: border-box; }
  html, body { width: 1200px; height: 900px; overflow: hidden; }
  body {
    background: var(--stage);
    display: flex;
    align-items: center;
    justify-content: center;
    gap: 60px;
  }
  .club-card {
    position: relative;
    width: 520px;
    height: 327px;
    border-radius: 22px;
    overflow: hidden;
    box-shadow: 0 14px 30px rgba(0,0,0,0.45);
  }
  .card-texture {
    position: absolute;
    inset: 0;
  }
  .club-card--front { background: var(--card-light); }
  .club-card--front .card-texture {
    background:
      radial-gradient(ellipse 60% 40% at 30% 80%, rgba(205,191,184,0.55), transparent 70%),
      radial-gradient(ellipse 50% 35% at 75% 20%, rgba(205,191,184,0.45), transparent 70%),
      var(--card-light);
  }
  .club-card--back { background: var(--card-dark); }
  .club-card--back .card-texture {
    background:
      radial-gradient(ellipse 45% 35% at 25% 20%, var(--swirl-red), transparent 70%),
      radial-gradient(ellipse 55% 40% at 80% 75%, var(--swirl-red), transparent 72%),
      radial-gradient(ellipse 70% 60% at 55% 45%, var(--swirl-deep), transparent 80%),
      var(--card-dark);
  }
  .brand-lockup {
    position: absolute;
    left: 58px;
    top: 112px;
    display: flex;
    align-items: center;
    gap: 20px;
  }
  .brand-mark { flex: none; }
  .brand-text { display: flex; flex-direction: column; }
  .brand-name {
    font-family: "Alfa Slab One", serif;
    font-size: 40px;
    line-height: 1;
    color: var(--brand-red);
  }
  .brand-service {
    font-family: "Roboto Slab", serif;
    font-weight: 800;
    font-size: 30px;
    line-height: 1.1;
    color: var(--ink);
  }
  .brand-tagline {
    font-family: "Cinzel", serif;
    font-weight: 500;
    font-size: 11px;
    letter-spacing: 0.3px;
    color: var(--ink);
    margin-top: 3px;
    padding-left: 42px;
  }
  .card-url {
    position: absolute;
    left: 0;
    right: 0;
    bottom: 26px;
    text-align: center;
    font-family: "Tinos", serif;
    font-size: 15px;
    letter-spacing: 1px;
    color: var(--ink-soft);
  }
  .studio-block {
    position: absolute;
    inset: 0;
    display: flex;
    flex-direction: column;
    align-items: center;
    justify-content: center;
    color: var(--silver);
    text-shadow: 0 1px 2px rgba(0,0,0,0.5);
  }
  .studio-title {
    display: flex;
    flex-direction: column;
    align-items: center;
    font-family: "Tinos", serif;
    font-weight: 700;
    font-size: 40px;
    line-height: 1.2;
    letter-spacing: 1.5px;
    word-spacing: 6px;
  }
  .studio-subtitle {
    margin-top: 14px;
    font-family: "Tinos", serif;
    font-size: 15px;
    letter-spacing: 2px;
    color: var(--silver-soft);
  }
</style>
</head>
<body>
  <section class="club-card club-card--front">
    <div class="card-texture" role="img" aria-label="Soft pale swirling marble texture"></div>
    <div class="brand-lockup">
      <svg class="brand-mark" width="86" height="86" viewBox="0 0 86 86" aria-hidden="true">
        <circle cx="43" cy="43" r="39" fill="#ffffff" stroke="#111111" stroke-width="7"/>
      </svg>
      <div class="brand-text">
        <span class="brand-name">Vorniq fit</span>
        <span class="brand-service">Personal training</span>
        <span class="brand-tagline">Your health is our challenge</span>
      </div>
    </div>
    <p class="card-url">www.Vorniqfit.nl</p>
  </section>

  <section class="club-card club-card--back">
    <div class="card-texture" role="img" aria-label="Dark swirling red and black marble texture"></div>
    <div class="studio-block">
      <h1 class="studio-title">
        <span>Personal Training</span>
        <span>Studio Marwijk</span>
      </h1>
      <p class="studio-subtitle">personal training and fitness</p>
    </div>
  </section>
</body>
</html>
```